professional business card design

Business card design. Photos have been uploaded and i am open to the designer choosing which photos to use. Would like the card to be mostyly in a grey scale design with black, whites, silver & grey colours. I have added copy of our flyer as would like on the back side of card our services to be listed. Do not use any bright colurs such as blue red green or yellow. i need to be able to edit the phone number and naem in the final card design submitted.

Target Market(s)

Clients

Industry/Entity Type

earhmovibng and transport

Contact Information for Business Card

Director Name, address, email, phone number and services

Colors

Designer to choose only greyscale colors for use in the design.

Requirements
Should not have
• no yellow, red, blue or green

```html
<!DOCTYPE html>
<html lang="en">
<head>
<meta charset="utf-8">
<title>RHX Pty Ltd – Business Card</title>
<link href="https://fonts.googleapis.com/css2?family=Source+Sans+3:wght@400;600&family=Crimson+Text&family=Oswald:wght@500;600&display=swap" rel="stylesheet">
<style>
  :root{
    --stage:#9a9b9a;
    --card:#050505;
    --accent:#c4c4c4;
    --accent-light:#e6e6e6;
    --accent-dark:#8f8f8f;
    --ink:#0a0a0a;
    --white:#ffffff;
    --muted:#b3b3b3;
    --silver:#c9c9c9;
  }
  *{margin:0;padding:0;box-sizing:border-box}
  html,body{width:1200px;height:1200px;overflow:hidden}
  body{background:var(--stage);position:relative;font-family:"Source Sans 3",sans-serif}
  .card{position:absolute;left:231px;width:736px;height:451px;background:var(--card);overflow:hidden}
  .card--front{top:116px}
  .card--back{top:631px;background:radial-gradient(ellipse at 35% 40%,#262626 0%,#111 55%,#050505 100%)}

  .hero{position:absolute;left:0;top:0;width:736px;height:294px;
    background:linear-gradient(180deg,#0a0a0a 0%,#1e1e1e 35%,#2a2624 60%,#8a5a3a 82%,#b07a52 100%)}
  .brand-name{position:absolute;left:0;top:22px;width:736px;text-align:center;
    font-family:"Source Sans 3",sans-serif;font-weight:600;font-size:88px;letter-spacing:6px;color:var(--silver);line-height:1}
  .silver-bar{position:absolute;left:150px;top:294px;width:440px;height:14px;
    background:linear-gradient(90deg,transparent,#888 30%,#fff 50%,#888 70%,transparent)}

  .contact{position:absolute;left:38px;top:324px;color:var(--white);font-size:18px;line-height:24px}
  .contact li{list-style:none;display:flex;align-items:center;gap:10px}
  .contact svg{width:15px;height:15px;flex:none}
  .contact .address{display:block;margin-top:3px}
  .contact .address span{color:var(--muted)}

  .company-tag{position:absolute;left:551px;top:321px;width:185px;height:38px;
    background:linear-gradient(180deg,var(--accent-light),var(--accent) 55%,var(--accent-dark));
    border-radius:14px 0 0 14px;color:var(--ink);font-size:28px;line-height:38px;padding-left:10px;white-space:nowrap}
  .person-name{position:absolute;right:40px;top:366px;color:var(--white);font-size:30px;line-height:36px}
  .person-role{position:absolute;right:40px;top:404px;color:var(--muted);font-size:20px;line-height:24px}

  .services-tag{position:absolute;left:40px;top:42px;width:218px;height:32px;
    background:linear-gradient(180deg,var(--accent-light),var(--accent) 55%,var(--accent-dark));border-radius:8px;
    color:var(--ink);font-family:"Oswald",sans-serif;font-weight:600;font-size:22px;letter-spacing:2px;line-height:32px;text-align:center}
  .services{position:absolute;top:98px;font-family:"Crimson Text",serif;font-size:21px;line-height:28px;color:var(--white)}
  .services--left{left:40px}
  .services--right{left:490px}
  .services li{list-style:none;padding-left:18px;position:relative}
  .services li::before{content:"";position:absolute;left:1px;top:12px;width:7px;height:7px;border-radius:50%;background:var(--accent)}

  .accent-bar{position:absolute;left:0;top:331px;width:26px;height:67px;
    background:linear-gradient(90deg,var(--accent-dark),var(--accent-light));border-radius:0 6px 6px 0}
  .note{position:absolute;left:40px;top:340px;width:370px;font-family:"Oswald",sans-serif;font-weight:500;
    font-size:18px;line-height:23px;color:var(--white)}
  .truck-photo{position:absolute;left:421px;top:245px;width:292px;height:180px;
    background:radial-gradient(ellipse at 50% 60%,#9aa3ad 0%,#5b5f63 45%,transparent 75%)}
</style>
</head>
<body>
  <section class="card card--front">
    <div class="hero" role="img" aria-label="Road train with three tipper trailers on a red desert track, dark hex mesh backdrop"></div>
    <div class="brand-name">RHX</div>
    <div class="silver-bar"></div>
    <ul class="contact">
      <li><svg viewBox="0 0 16 16"><path fill="#c4c4c4" d="M3 1l3 3-2 2c1 2 3 4 5 5l2-2 3 3-2 2C7 14 2 9 1 3z"/></svg>100-200-300</li>
      <li><svg viewBox="0 0 16 16"><rect x="1" y="3" width="14" height="10" fill="none" stroke="#c4c4c4" stroke-width="1.6"/><path d="M1 3l7 6 7-6" fill="none" stroke="#c4c4c4" stroke-width="1.6"/></svg>hello@rhxhaul.com</li>
      <li><svg viewBox="0 0 16 16"><circle cx="8" cy="8" r="6.5" fill="none" stroke="#c4c4c4" stroke-width="1.3"/><ellipse cx="8" cy="8" rx="3" ry="6.5" fill="none" stroke="#c4c4c4" stroke-width="1.2"/><path d="M1.5 8h13M2.5 5h11M2.5 11h11" stroke="#c4c4c4" stroke-width="1.1"/></svg>rhxhaul.com</li>
      <li class="address"><span>Depot:</span> Lot 114, Red Gum Track, Sandy Flat</li>
    </ul>
    <div class="company-tag">RHX Pty Ltd</div>
    <div class="person-name">MARK DALTON</div>
    <div class="person-role">Director</div>
  </section>

  <section class="card card--back">
    <div class="services-tag">OUR SERVICES</div>
    <ul class="services services--left">
      <li>Over Size Loads/Hot Shot Loads</li>
      <li>Heavy Vehicle Recovery Services</li>
      <li>Potable Water Deliveries</li>
      <li>Road Building / Maintenance</li>
      <li>Sand &amp; Metal Supply &amp; Cartage</li>
      <li>Mine Site accredited equipment &amp; Operators</li>
    </ul>
    <ul class="services services--right">
      <li>Road Train Tippers</li>
      <li>Road Train Tankers</li>
      <li>Road Train Flat Tops</li>
      <li>Drop Deck Trailers</li>
      <li>Earthworks</li>
    </ul>
    <div class="accent-bar"></div>
    <p class="note">We offer a large range of services not listed.<br>So call us today for a personalised quote to<br>suit your needs.</p>
    <div class="truck-photo" role="img" aria-label="Prime mover hauling a grader on a drop deck trailer"></div>
  </section>
</body>
</html>
```